App-Design für Vergleichsportal für Reparaturen
Zielgruppe
Flickwerkzentrale ist das Vergleichsportal für Reparaturen in deiner Nähe. Egal ob du eine Werkstatt für dein Smartphone, Tablet, Laptop, Computer, Smartwatch oder Spielkonsole suchst. Mit uns findest du deine passende Reparaturwerkstat in deiner Nähe mit dem besten Preis für dich. Du kannst dich direkt über unser Portal deinen Reparaturauftrag erhalten und wirst durch unser Sicher Kaufen Käuferschutz und unser VORMANT Treuhandschutz abgesichert.
Aufgabenstellung
Unter Flickwerkzentrale.de kann das aktuelle Design angeschaut werden. Die Farbe sollten übernommen werden.
Über die Startseite kann der Kunde sein Gerät, Service sowie seine Adresse eingeben. Auf der Vergleichsseite bekommt der Kunde die Übersicht welche Reparaturwerkstätten es gibt, zu welche Preisen die ausgewählte Dienstleistung angeboten wird. Wenn der Kunde auf den Button 'Jetzt Online Bestpreis buchen' drückt, dann kommt der Kunde in den Warenkorb. Im Warenkorb können noch weitere Dienstleistungen und Produkte dazugebucht werden. Und anschließend kommt der Kunde in die Kasse und kann der Bestellvorgang beenden. Die Benutzerführung sollte einfach sein. Im Fokus steht die Vergleichsseite. Dort sollte der Kunde ca. 4 Werkstätten auf einen Blick sehen können. Könnte ausschauen wie bei Tarifblick in der Kategorie Mobilfunk.
Die Vergleichseite sollte auf jeden Fall folgende Elemente enthalten:
- Entfernung zur Werkstatt in Meter bzw. Kilometer
- Logo der Werkstatt
- Name der Werkstatt
- Bewertungssterne der Werkstatt
- Reparaturzeit und Ersatzeilverfügbarkeit
- Reparaturpreis (Platz sollte auch bei Auswahl von 2 Dienstleistungen vorhanden sein)
- Rabattanzeige
- Qualitätssiegel (noch nicht vorhanden)
- Anzeige von Verknappung (z. B. noch 3 Termin frei)
- Qualitätsmerkmale (z. B. 12 Monate Garantie)
Die Merkmale Öffnungszeiten, Adresse, Kostenpflichtige Zusatzleistungen können aus Platzgründen in den Warenkorbseite wandern außer es gibt eine schöne und einfache Lösung.
In der Warenkorbseite kann dazu auch die Tarifblick Seite dienen.
Bei allen sollte auf die Benutzerfreundlichkeit geachtet werden.
Bei offenen Frage stehe ich zur Verfügung und freue mich auf viele Designs.
Vielen DANK im Voraus!

```html
<!DOCTYPE html>
<html lang="de">
<head>
<meta charset="utf-8">
<title>Flickwerkzentrale – Warenkorb</title>
<link rel="stylesheet" href="https://fonts.googleapis.com/css2?family=Source+Sans+3:wght@300;400;600&display=swap">
<style>
  :root{
    --stage:#262626;
    --teal:#244b5d;
    --green:#8ab833;
    --green-text:#8ab833;
    --page:#f0f2f4;
    --white:#ffffff;
    --ink:#1e2a30;
    --line:#d5dadd;
    --card-border:#2f5567;
    --placeholder:#c9ced2;
  }
  *{box-sizing:border-box;margin:0;padding:0}
  html,body{width:1200px;height:728px;overflow:hidden}
  body{background:var(--stage);font-family:"Source Sans 3",sans-serif;font-weight:400;color:var(--ink);position:relative}

  .screen{position:absolute;left:439px;top:16px;width:322px;height:696px;background:var(--page);overflow:hidden}

  .status-bar{height:28px;background:var(--white);display:flex;align-items:center;justify-content:space-between;padding:0 14px 0 16px}
  .status-time{font-size:12px;font-weight:600}
  .status-icons{display:flex;gap:4px;align-items:center}

  .app-header{height:42px;background:var(--white);display:flex;align-items:center;justify-content:space-between;padding:0 14px 0 12px}
  .brand{display:flex;align-items:center;gap:5px;font-size:12px;font-weight:400;color:var(--teal)}
  .brand-dot{width:10px;height:10px;border-radius:50%;background:var(--green)}
  .menu-toggle{width:19px;display:flex;flex-direction:column;gap:5px}
  .menu-toggle span{height:1.5px;background:var(--teal)}

  .page-title{height:36px;background:var(--teal);color:var(--green-text);font-size:14px;font-weight:400;display:flex;align-items:center;justify-content:center}

  .card{position:absolute;left:25px;width:271px;background:var(--white);border:1px solid var(--card-border)}

  .cart-item{top:130px;height:80px}
  .product-image{position:absolute;left:8px;top:7px;width:32px;height:64px;border-radius:5px;background:var(--placeholder)}
  .item-line{position:absolute;left:51px;font-size:7.5px;line-height:1;font-weight:400}
  .item-title{top:9px}
  .item-part{top:19px;color:var(--green-text)}
  .item-device{top:35px}
  .item-qty{top:56px;font-size:6.5px}
  .item-price{position:absolute;right:14px;top:55px;font-size:9px;font-weight:400}
  .remove-item{position:absolute;right:5px;top:4px;width:14px;height:14px;background:var(--teal);display:flex;align-items:center;justify-content:center}

  .voucher{position:absolute;left:25px;top:224px;width:271px;height:31px;background:var(--teal);color:var(--green-text);font-size:12px;font-weight:300;display:flex;align-items:center;justify-content:space-between;padding:0 10px}

  .summary{top:269px;height:193px;padding:0 8px}
  .sum-row{display:flex;justify-content:space-between;align-items:center;font-size:7.5px;line-height:11px;font-weight:400}
  .sum-block{border-bottom:1px solid var(--line);padding:6px 0}
  .sum-total{color:var(--green-text)}
  .repair-time{font-size:7.5px;padding:8px 0 9px;font-weight:400}
  .checkout{display:flex;align-items:center;justify-content:center;gap:5px;height:28px;background:var(--green);color:var(--white);font-size:11.5px;font-weight:400;border-radius:1px}
  .legal-link{text-align:center;color:var(--green-text);font-size:6.5px;margin-top:6px;font-weight:400}

  .options{top:478px;height:192px;padding:8px 8px 0}
  .options-title{font-size:7.5px;font-weight:600;margin-bottom:10px}
  .options-group{font-size:7.5px;font-weight:400;margin:0 0 3px}
  .option{display:flex;align-items:center;height:24px;background:var(--green);color:var(--white);font-size:8.5px;font-weight:400;padding:0 6px;margin-bottom:2px}
  .option + .options-group{margin-top:8px}
  .option-name{flex:1;margin-left:5px}
  .option-price{margin-right:10px}
  .info{width:9px;height:9px;border-radius:50%;background:var(--teal);color:var(--white);font-size:6px;display:flex;align-items:center;justify-content:center;font-weight:600}
</style>
</head>
<body>
<main class="screen">
  <div class="status-bar">
    <span class="status-time">9:41</span>
    <span class="status-icons">
      <svg width="14" height="9" viewBox="0 0 14 9"><rect x="0" y="6" width="2.5" height="3" fill="#1e2a30"/><rect x="3.5" y="4" width="2.5" height="5" fill="#1e2a30"/><rect x="7" y="2" width="2.5" height="7" fill="#1e2a30"/><rect x="10.5" y="0" width="2.5" height="9" fill="#1e2a30"/></svg>
      <svg width="12" height="9" viewBox="0 0 12 9"><path d="M1 3.5a7 7 0 0 1 10 0M3 5.5a4 4 0 0 1 6 0" stroke="#1e2a30" stroke-width="1.4" fill="none"/><circle cx="6" cy="7.8" r="1.1" fill="#1e2a30"/></svg>
      <svg width="19" height="9" viewBox="0 0 19 9"><rect x="0.5" y="0.5" width="16" height="8" rx="2" stroke="#1e2a30" fill="none"/><rect x="2" y="2" width="13" height="5" rx="1" fill="#1e2a30"/><rect x="17.3" y="3" width="1.2" height="3" fill="#1e2a30"/></svg>
    </span>
  </div>

  <header class="app-header">
    <div class="brand"><span class="brand-dot"></span>Flickwerkzentrale</div>
    <div class="menu-toggle"><span></span><span></span><span></span></div>
  </header>

  <h1 class="page-title">Warenkorb</h1>

  <section class="card cart-item">
    <div class="product-image" role="img" aria-label="Produktfoto des Smartphones"></div>
    <p class="item-line item-title">Verbindungs &amp; Anschlusselemente:</p>
    <p class="item-line item-part">Akku</p>
    <p class="item-line item-device">Telio 6s</p>
    <p class="item-line item-qty">1 x 69,00€</p>
    <p class="item-price">69,00€</p>
    <span class="remove-item"><svg width="8" height="8" viewBox="0 0 8 8"><path d="M1 1l6 6M7 1L1 7" stroke="#8ab833" stroke-width="1"/></svg></span>
  </section>

  <div class="voucher">
    <span>Gutschein</span>
    <svg width="9" height="5" viewBox="0 0 9 5"><path d="M1 1l3.5 3L8 1" stroke="#8ab833" stroke-width="1" fill="none"/></svg>
  </div>

  <section class="card summary">
    <div class="sum-block">
      <div class="sum-row"><span>Zwischensumme:</span><span>69,00€</span></div>
      <div class="sum-row"><span>Rabatt:<br>Telio Akku (-40.00% außer Shopartikel)</span><span>-27,60€</span></div>
    </div>
    <div class="sum-block">
      <div class="sum-row"><span>kein Versand,<br>Abholung in der Werkstatt ausgewählt</span><span>0,00€</span></div>
    </div>
    <div class="sum-block">
      <div class="sum-row sum-total"><span>Gesamtpreis:</span><span>41,40€</span></div>
    </div>
    <p class="repair-time">Reparaturzeit: ca. 1 Stunde</p>
    <a class="checkout">Weiter zur Kasse
      <svg width="6" height="9" viewBox="0 0 6 9"><path d="M1 1l3.5 3.5L1 8" stroke="#fff" stroke-width="1.3" fill="none"/></svg>
    </a>
    <p class="legal-link">Rechtliche Hinweise der Werkstatt</p>
  </section>

  <section class="card options">
    <h2 class="options-title">Weitere Optionen</h2>
    <p class="options-group">Garantie</p>
    <div class="option"><svg width="12" height="10" viewBox="0 0 12 10"><path d="M0.5 1h2l1.5 6h6l1.5-4.5H3" stroke="#fff" stroke-width="1" fill="none"/><circle cx="4.8" cy="8.7" r="0.9" fill="#fff"/><circle cx="9" cy="8.7" r="0.9" fill="#fff"/></svg><span class="option-name">6 Monate</span><span class="option-price">0,00 €</span><span class="info">i</span></div>
    <p class="options-group">Service</p>
    <div class="option"><svg width="12" height="10" viewBox="0 0 12 10"><path d="M0.5 1h2l1.5 6h6l1.5-4.5H3" stroke="#fff" stroke-width="1" fill="none"/><circle cx="4.8" cy="8.7" r="0.9" fill="#fff"/><circle cx="9" cy="8.7" r="0.9" fill="#fff"/></svg><span class="option-name">Bringservice</span><span class="option-price">15,00 €</span><span class="info">i</span></div>
    <div class="option" style="margin-top:3px"><svg width="12" height="10" viewBox="0 0 12 10"><path d="M0.5 1h2l1.5 6h6l1.5-4.5H3" stroke="#fff" stroke-width="1" fill="none"/><circle cx="4.8" cy="8.7" r="0.9" fill="#fff"/><circle cx="9" cy="8.7" r="0.9" fill="#fff"/></svg><span class="option-name">Abholservice</span><span class="option-price">15,00 €</span><span class="info">i</span></div>
    <p class="options-group">Expressreparatur</p>
    <div class="option"><svg width="12" height="10" viewBox="0 0 12 10"><path d="M0.5 1h2l1.5 6h6l1.5-4.5H3" stroke="#fff" stroke-width="1" fill="none"/><circle cx="4.8" cy="8.7" r="0.9" fill="#fff"/><circle cx="9" cy="8.7" r="0.9" fill="#fff"/></svg><span class="option-name">in 60 Minuten</span><span class="option-price">79,00 €</span><span class="info">i</span></div>
  </section>
</main>
</body>
</html>
```